Business card for law firm

Need business card for new law firm. Think confident, authoritative, conservative, but not stuffy or old-fashioned.

Contact Information for Business Card

Content for card - logo (uploaded), plus the following:

Paul Whitcombe (larger font)
Managing Partner (larger font, but not as large as name)
Level 9, 7 Ferris Lane
Sydney NSW 2000
Main Tel 02 9364 2710
Direct Tel 02 8472 3159
Email paul@qvlegal.com.au
www.qvlegal.com.au

Letterhead design should include logo plus:
Level 9, 7 Ferris Lane
Sydney NSW 2000
Tel 02 8472 3159
www.qvlegal.com.au

```html
<!DOCTYPE html>
<html lang="en">
<head>
<meta charset="utf-8">
<title>Quayvale Legal – Business Card</title>
<link rel="stylesheet" href="https://fonts.googleapis.com/css2?family=Jost:wght@400;500&family=Roboto:wght@400;700&display=swap">
<style>
  :root {
    --backdrop: #3b3b3d;
    --card-grey: #8c8c8e;
    --card-grey-light: #9a9a9c;
    --card-black: #0c0c0d;
    --card-navy: #0c1e57;
    --navy-mark: #1a2f7a;
    --ink-dark: #161616;
    --ink-light: #ffffff;
    --ink-soft: #d9def0;
  }
  * { box-sizing: border-box; margin: 0; padding: 0; }
  html, body {
    width: 1200px; height: 1000px; overflow: hidden;
    background: var(--backdrop);
  }
  .stage {
    position: relative; width: 1200px; height: 1000px;
  }
  .card {
    position: absolute; width: 640px; height: 390px;
    border-radius: 26px; overflow: hidden;
    box-shadow: 0 18px 40px rgba(0,0,0,0.45);
  }

  /* Front */
  .card--front {
    left: 280px; top: 70px;
    background: linear-gradient(135deg, var(--card-grey-light), var(--card-grey));
  }
  .front-band {
    position: absolute; left: 0; top: 0; width: 150px; height: 100%;
  }
  .front-brand {
    position: absolute; right: 56px; top: 150px;
    display: flex; flex-direction: column; align-items: flex-end; gap: 22px;
  }
  .brand {
    display: flex; align-items: center; gap: 16px;
  }
  .brand-square {
    width: 30px; height: 30px;
  }
  .brand-square--navy { background: var(--navy-mark); }
  .brand-square--white { background: var(--ink-light); }
  .brand-name {
    font-family: "Jost", sans-serif; font-weight: 500;
    font-size: 40px; letter-spacing: 5px; text-transform: uppercase;
  }
  .card--front .brand-name { color: var(--ink-dark); }
  .front-web {
    font-family: "Jost", sans-serif; font-weight: 400;
    font-size: 18px; letter-spacing: 1px; color: var(--ink-dark);
  }

  /* Back */
  .card--back {
    left: 280px; top: 540px;
    background: var(--card-navy);
    color: var(--ink-light);
  }
  .holder {
    position: absolute; left: 44px; top: 40px;
  }
  .holder-name {
    font-family: "Roboto", sans-serif; font-weight: 700;
    font-size: 24px; text-transform: uppercase; letter-spacing: 0.5px;
  }
  .holder-title {
    font-family: "Roboto", sans-serif; font-weight: 400;
    font-size: 16px; color: var(--ink-soft); margin-top: 2px;
  }
  .contact {
    list-style: none; margin-top: 18px;
    font-family: "Jost", sans-serif; font-size: 15px; line-height: 1.55;
    color: var(--ink-soft);
  }
  .back-brand {
    position: absolute; right: 48px; bottom: 40px;
    display: flex; flex-direction: column; align-items: flex-end; gap: 18px;
  }
  .card--back .brand-name { color: var(--ink-light); font-size: 36px; }
  .address {
    font-family: "Jost", sans-serif; font-weight: 400;
    font-size: 16px; letter-spacing: 0.5px;
  }
</style>
</head>
<body>
<main class="stage">

  <section class="card card--front" aria-label="Card front">
    <svg class="front-band" viewBox="0 0 150 390" role="img" aria-label="Dark decorative swoosh panel">
      <rect width="150" height="390" fill="var(--card-black)"/>
    </svg>
    <div class="front-brand">
      <div class="brand">
        <span class="brand-square brand-square--navy"></span>
        <span class="brand-name">Quayvale Legal</span>
      </div>
      <p class="front-web">www.qvlegal.com.au</p>
    </div>
  </section>

  <section class="card card--back" aria-label="Card back">
    <div class="holder">
      <h1 class="holder-name">Paul Whitcombe</h1>
      <p class="holder-title">Managing Partner</p>
      <ul class="contact">
        <li>Main Tel 02 9364 2710 | Direct Tel 02 8472 3159</li>
        <li>E: paul@qvlegal.com.au | W: www.qvlegal.com</li>
      </ul>
    </div>
    <div class="back-brand">
      <div class="brand">
        <span class="brand-square brand-square--white"></span>
        <span class="brand-name">Quayvale Legal</span>
      </div>
      <p class="address">Level 9, 7 Ferris Lane Sydney NSW 2000</p>
    </div>
  </section>

</main>
</body>
</html>
```